Business Cards for new orthopaedic surgery practice

My husband and I are starting our own orthopaedic surgery practice. We are looking for a business card that is uniform, but one will have my name/title and the other will have his. You can just create one design with my name on it for now. But when I choose your design as the winning design I will ask that you add another copy with his name/title.

We are looking for classy, simple, elite all in one. We like dark blues/a little gold/yellow. Something that goes with our logo. We want our logo incorporated. Here is all the info you need:
Business name: RV Bone & Vitality Center
Location: 38517 North Willowmere Ave
Coral Springs, FL 33071
Phone: 954-218-4063
Fax: 954-582-7341
Email: info@myrvbonecare.example

Names: Lydia Vance, M.D.
Board Certified Hand and Upper Extremity Surgeon

Ebo Dansu, M.D.
Board Certified Hip & Knee Replacement/General Orthopaedic Surgeon

Can decide what you want to put on the back. Maybe a slogan:
Steady Hands. Lasting Strength

I am just going to upload our logo. The only thing is if we select you as the winning design, the location, and phone numbers may change. We will need your help to update that once fully solidified.

Industry/Entity Type

Medical

Contact Information for Business Card

Colors
0054AA
0677BA
7BADD7
CADEEF
E8F1F8
0094D4
00A9DD
6FCCEA
C7EBF8
E9F6FB

Requirements
Must have
• class, appeal,
Should not have
• We want to air on the side of masculine if we are looking at masculine vs. feminine feel. But we still want it classy, sophisticated, and something we will love

```html
<!DOCTYPE html>
<html lang="en">
<head>
<meta charset="utf-8">
<title>RV Bone &amp; Vitality Center — Business Card</title>
<link rel="stylesheet" href="https://fonts.googleapis.com/css2?family=Marcellus&family=Roboto:wght@400&display=swap">
<style>
  :root {
    --backdrop: #8f8f8f;
    --paper: #ffffff;
    --navy: #213f88;
    --cyan: #1bb6e0;
    --ink: #4a4a4a;
    --back-blue: #2b3690;
    --back-blue-deep: #23307f;
  }
  * { box-sizing: border-box; margin: 0; padding: 0; }
  html, body { width: 1188px; height: 1200px; overflow: hidden; }
  body { background: var(--backdrop); position: relative; }

  .card {
    position: absolute;
    left: 245px;
    width: 696px;
    height: 386px;
    overflow: hidden;
  }
  .card--front { top: 159px; background: var(--paper); }
  .card--back {
    top: 627px;
    background: linear-gradient(135deg, var(--back-blue) 0%, var(--back-blue-deep) 100%);
  }

  .practice-name {
    position: absolute;
    left: 76px;
    top: 196px;
    width: 310px;
    text-align: center;
    font-family: "Marcellus", serif;
    font-size: 23px;
    line-height: 30px;
    color: var(--navy);
    letter-spacing: 0.5px;
  }

  .divider {
    position: absolute;
    left: 379px;
    top: 89px;
    width: 1px;
    height: 215px;
    background: var(--cyan);
  }

  .contact { position: absolute; left: 398px; top: 89px; width: 290px; }
  .contact__name {
    font-family: "Marcellus", serif;
    font-size: 21px;
    line-height: 26px;
    color: var(--navy);
    white-space: nowrap;
  }
  .contact__title {
    font-family: "Roboto", sans-serif;
    font-size: 16px;
    line-height: 21px;
    color: var(--cyan);
  }
  .contact__list { list-style: none; margin-top: 17px; }
  .contact__item {
    display: flex;
    align-items: flex-start;
    font-family: "Roboto", sans-serif;
    font-size: 17px;
    line-height: 21px;
    color: var(--ink);
    margin-bottom: 1.5px;
    white-space: nowrap;
  }
  .contact__item--address { margin-bottom: 3px; }
  .contact__icon { width: 16px; height: 16px; margin: 3px 7px 0 0; flex: none; fill: var(--navy); }

  .tagline-band {
    position: absolute;
    left: 0; bottom: 0;
    width: 100%;
    height: 28px;
    background: var(--navy);
  }
  .tagline-band__accent { position: absolute; right: 0; top: 0; }
  .tagline-band__text {
    position: absolute;
    left: 0; top: 0;
    width: 696px;
    line-height: 28px;
    text-align: center;
    font-family: "Marcellus", serif;
    font-size: 14px;
    letter-spacing: 1px;
    color: var(--paper);
  }

  .monogram-field { position: absolute; inset: 0; }
</style>
</head>
<body>

<section class="card card--front" aria-label="Business card front">
  <div class="practice-name">RV Bone &amp;<br>Vitality Center</div>

  <div class="divider"></div>

  <div class="contact">
    <p class="contact__name">LYDIA VANCE, M.D.</p>
    <p class="contact__title">Board Certified Hand &amp;<br>Upper Extremity Surgeon</p>
    <ul class="contact__list">
      <li class="contact__item contact__item--address">
        <svg class="contact__icon" viewBox="0 0 16 16" aria-hidden="true"><path d="M8 0a5.5 5.5 0 0 0-5.5 5.5C2.5 9.7 8 16 8 16s5.5-6.3 5.5-10.5A5.5 5.5 0 0 0 8 0zm0 8a2.3 2.3 0 1 1 0-4.6A2.3 2.3 0 0 1 8 8z"/></svg>
        <span>38517 North Willowmere Ave<br>Coral Springs, FL 33071</span>
      </li>
      <li class="contact__item">
        <svg class="contact__icon" viewBox="0 0 16 16" aria-hidden="true"><path d="M1 6c0-2 3-3.5 7-3.5S15 4 15 6v1.5h-3.5V6h-7v1.5H1z"/><path d="M4 8l1.5-2h5L12 8v5H4z"/></svg>
        <span>954-218-4063</span>
      </li>
      <li class="contact__item">
        <svg class="contact__icon" viewBox="0 0 16 16" aria-hidden="true"><path d="M4 1h8v4H4z"/><path d="M1 6h14v6h-3v3H4v-3H1zm4 4v4h6v-4z"/></svg>
        <span>954-582-7341</span>
      </li>
      <li class="contact__item">
        <svg class="contact__icon" viewBox="0 0 16 16" aria-hidden="true"><path d="M0 3h16v10H0z"/><path d="M0.5 3.5L8 9l7.5-5.5" fill="none" stroke="#fff" stroke-width="1.2"/></svg>
        <span>info@myrvbonecare.example</span>
      </li>
      <li class="contact__item">
        <svg class="contact__icon" viewBox="0 0 16 16" aria-hidden="true"><circle cx="8" cy="8" r="7.5"/><path d="M5 3.5c1.5.5 2 1.5 1 2.5S4 7.5 5 9s2 1 2 3M10.5 4c-1 1 0 2 1 2.5s2 0 2.5 1M9.5 10c1-.5 2 0 2.5 1.5" fill="none" stroke="#fff" stroke-width="1.1"/></svg>
        <span>www.lvancehand.example</span>
      </li>
    </ul>
  </div>

  <div class="tagline-band">
    <svg class="tagline-band__accent" width="102" height="28" viewBox="0 0 102 28" aria-hidden="true">
      <polygon points="18,0 102,0 102,28 0,28" fill="var(--cyan)"/>
      <polygon points="16,0 18.5,0 0.5,28 -2,28" fill="#fff"/>
    </svg>
    <p class="tagline-band__text">STEADY HANDS. LASTING STRENGTH</p>
  </div>
</section>

<section class="card card--back" aria-label="Business card back">
  <div class="monogram-field" role="img" aria-label="Embossed repeating pattern of the practice monogram in silver and blue tones, with one white monogram highlighted"></div>
</section>

</body>
</html>
```